Harborline Auto LLC

Car Dealer Customer Service
Address: 2874 Cresthaven Road, Shelbyville, TN 37162
web: www.harborlineautoxq.net
email: harborlineautoxq@mailnest.example
Phone: (931) 555-0148
Phone: (629) 555-0173

```html
<!DOCTYPE html>
<html lang="en">
<head>
<meta charset="utf-8">
<title>Harborline Auto LLC – Business Card</title>
<link rel="stylesheet" href="https://fonts.googleapis.com/css2?family=Lexend:wght@700&family=Oswald:wght@700&family=Poppins:wght@400&display=swap">
<style>
  :root {
    --backdrop: #2b2b2b;
    --brand-blue: #1c78a8;
    --brand-blue-deep: #176790;
    --brand-gold: #e0a73a;
    --paper: #f1f1f0;
    --ink: #1e1e1e;
    --white: #ffffff;
  }
  * { margin: 0; padding: 0; box-sizing: border-box; }
  html, body { width: 1200px; height: 1138px; overflow: hidden; background: var(--backdrop); }
  .canvas { position: relative; width: 1200px; height: 1138px; }

  .card {
    position: absolute;
    border-radius: 16px;
    overflow: hidden;
  }
  .card-front {
    left: 274px; top: 186px; width: 623px; height: 376px;
    background: linear-gradient(160deg, var(--brand-blue) 0%, var(--brand-blue-deep) 100%);
  }
  .card-back {
    left: 276px; top: 608px; width: 618px; height: 374px;
    background: var(--paper);
  }

  .front-emblem-circle {
    position: absolute;
    left: -46px; top: 18px;
    width: 344px; height: 344px;
    border-radius: 50%;
    background: #e9eef1;
  }
  .front-name {
    position: absolute;
    right: 41px; top: 56px;
    font-family: "Lexend", sans-serif;
    font-weight: 700;
    font-size: 26px;
    letter-spacing: 0.5px;
    color: var(--white);
  }
  .front-web {
    position: absolute;
    right: 41px; top: 320px;
    font-family: "Poppins", sans-serif;
    font-size: 15px;
    color: var(--white);
  }

  .wave { position: absolute; left: 0; top: 0; width: 618px; height: 374px; }

  .phone-list { position: absolute; left: 30px; top: 60px; list-style: none; }
  .phone-list li {
    display: flex; align-items: center; gap: 9px;
    font-family: "Oswald", sans-serif;
    font-weight: 700;
    font-size: 27px;
    line-height: 29px;
    color: var(--ink);
  }
  .phone-list svg { width: 20px; height: 18px; flex: none; }

  .back-mark {
    position: absolute;
    left: 406px; top: 48px;
    width: 112px; height: 112px;
    border-radius: 50%;
    background: var(--brand-blue);
  }
  .back-name {
    position: absolute;
    left: 462px; top: 212px;
    transform: translateX(-50%);
    white-space: nowrap;
    font-family: "Lexend", sans-serif;
    font-weight: 700;
    font-size: 24px;
    letter-spacing: 0.5px;
    color: var(--brand-blue);
  }

  .contact {
    position: absolute; left: 30px; top: 254px;
    font-family: "Poppins", sans-serif;
    font-size: 15px;
    color: var(--white);
  }
  .contact address { font-style: normal; line-height: 21px; margin-bottom: 6px; }
  .contact-line { display: flex; align-items: center; gap: 10px; line-height: 21px; }
  .contact-line svg { width: 14px; height: 12px; flex: none; }
</style>
</head>
<body>
<main class="canvas">

  <section class="card card-front" aria-label="Card front">
    <div class="front-emblem-circle"></div>
    <h1 class="front-name">HARBORLINE AUTO</h1>
    <p class="front-web">www.harborlineautoxq.net</p>
  </section>

  <section class="card card-back" aria-label="Card back">
    <svg class="wave" viewBox="0 0 618 374" aria-hidden="true">
      <path d="M0 206 C160 176 260 246 380 298 C470 334 560 322 618 306 L618 374 L0 374 Z" fill="var(--brand-blue)"/>
      <path d="M0 194 C160 164 262 234 382 286" fill="none" stroke="var(--brand-gold)" stroke-width="6"/>
      <path d="M330 284 C440 322 540 316 618 282 L618 292 C540 330 440 334 330 284 Z" fill="var(--brand-gold)"/>
    </svg>

    <ul class="phone-list">
      <li>
        <svg viewBox="0 0 20 18" aria-hidden="true"><path d="M2 4 C6 0 14 0 18 4 L16 7 L13 6 L13 4 C11 3 9 3 7 4 L7 6 L4 7 Z M5 9 L15 9 L17 17 L3 17 Z" fill="var(--brand-gold)"/></svg>
        (931) 555-0148
      </li>
      <li>
        <svg viewBox="0 0 20 18" aria-hidden="true"><path d="M2 4 C6 0 14 0 18 4 L16 7 L13 6 L13 4 C11 3 9 3 7 4 L7 6 L4 7 Z M5 9 L15 9 L17 17 L3 17 Z" fill="var(--brand-gold)"/></svg>
        (629) 555-0173
      </li>
    </ul>

    <div class="back-mark"></div>
    <h2 class="back-name">HARBORLINE AUTO</h2>

    <div class="contact">
      <address>2874 Cresthaven Road,<br>Shelbyville, TN 37162</address>
      <p class="contact-line">
        <svg viewBox="0 0 14 12" aria-hidden="true"><circle cx="7" cy="6" r="5.5" fill="none" stroke="var(--brand-gold)" stroke-width="1.5"/><path d="M1.5 6 H12.5 M7 0.5 C4 4 4 8 7 11.5 C10 8 10 4 7 0.5" fill="none" stroke="var(--brand-gold)" stroke-width="1.2"/></svg>
        www.harborlineautoxq.net
      </p>
      <p class="contact-line">
        <svg viewBox="0 0 14 12" aria-hidden="true"><rect x="0.5" y="1.5" width="13" height="9" fill="var(--brand-gold)"/><path d="M0.5 1.5 L7 7 L13.5 1.5" fill="none" stroke="var(--brand-blue)" stroke-width="1.2"/></svg>
        harborlineautoxq@mailnest.example
      </p>
    </div>
  </section>

</main>
</body>
</html>
```